DeskHarbor - Coworking website design

DeskHarbor is a new global coworking brand, growing fast and establishing stylish locations and communities that inspire innovation and collaboration all around the world.
The project includes a complete website design, focused on delivering the company’s values and messages, provide information to site visitors and to generate leads.

Please review the attached design brief, for more information.

Target Market(s)

Both men and women. Decision makers in:
Small & medium businesses in various fields, but mainly technology firms (Startups or established brands).
Global enterprises.
Dynamic “new generation” companies.
Press

Number of Pages Required

2 page

Requirements
Must have
• Project Scope & deliverables:
• Concept and design for :
• Home page
• Deliver the values mentioned above.
• Showcase the cities in which the company has locations in.
• Show customer testimonials.
• Provide an interface (form) for booking a tour and/or leaving contact details for more information (two alternatives)
• Coworking location page - Each location is in the coolest part of a different major city, and has its own address, set of amenities (kitchen, fast internet etc,), area information (public transportation accessibility, sites near by, bars and restaurants in walking distance) and pricing for private offices (based on number of people per office). Each location page must have an interface to book a location tour.
• Site Navigation (header & footer) - allow simple navigation between multiple city pages, location pages and homepage. Growth of up to 50 locations in 25 cities.
• The navigation should account for Navigation to additional pages (not commissioned in this project) such as:
• Locations
• Enterprise
• Special promotions
• Blog
• Contact us
• About us
• Note - the site should account for geolocation variable display, showing different content for different locations.
• Deliverables must include all editable graphic files (photoshop or similar), as follows:
• Home page - Desktop view (preferably both)
• Location page - Mobile web view (preferably both)
• Navigation - both options

```html
<!DOCTYPE html>
<html lang="en">
<head>
<meta charset="utf-8">
<title>DeskHarbor – Coworking</title>
<link rel="stylesheet" href="https://fonts.googleapis.com/css2?family=Open+Sans:wght@400;600;700;800&display=swap">
<style>
:root{
  --orange:#f5874a;
  --orange-dark:#ee7a35;
  --ink:#222;
  --text:#555;
  --cream:#fdf4ec;
  --dark:#2a2a2a;
  --darker:#1f1f1f;
  --grey-bg:#eeeeee;
  --map:#c9c9c9;
  --white:#fff;
}
*{box-sizing:border-box;margin:0;padding:0}
html,body{width:1200px;height:4225px;overflow:hidden}
body{font-family:"Open Sans",Arial,sans-serif;color:var(--text);background:var(--white);position:relative}
section,header,footer{position:relative;width:1200px;overflow:hidden}

/* header */
.site-header{height:113px;display:flex;align-items:center;justify-content:space-between;padding:0 100px}
.brand{font-weight:800;font-size:27px;color:var(--orange);letter-spacing:.5px;text-transform:uppercase}
.main-nav{display:flex;height:113px;align-items:center;margin-right:-8px}
.main-nav a{font-size:17px;color:var(--ink);text-decoration:none;padding:0 13px;height:113px;display:flex;align-items:center}
.main-nav a.active{background:var(--orange);color:var(--white);padding:0 22px}

/* hero */
.hero{height:512px}
.hero-photo{position:absolute;inset:0;background:linear-gradient(110deg,#1b1d22 0%,#3a3d44 35%,#55585e 55%,#2a2c31 80%,#1a1b1f 100%)}
.hero-copy{position:absolute;right:100px;top:120px;text-align:right;color:var(--white)}
.hero-title{font-size:56px;font-weight:800;letter-spacing:1px;text-transform:uppercase}
.hero-tag{font-size:26px;letter-spacing:8px;margin-top:6px;text-transform:uppercase}
.btn-outline-light{display:inline-block;margin-top:46px;border:2px solid var(--white);color:var(--white);font-size:15px;font-weight:600;padding:14px 18px;text-transform:uppercase}
.slider-dots{position:absolute;right:12px;top:160px;display:flex;flex-direction:column;gap:11px}
.slider-dots span{width:17px;height:17px;border-radius:50%;background:#ddd}
.slider-dots span.on{background:var(--orange)}
.scroll-notch{position:absolute;left:560px;bottom:0}

/* about */
.about{height:468px;text-align:center}
.section-title{font-size:28px;font-weight:700;color:var(--orange);text-transform:uppercase}
.rule{width:120px;height:2px;background:var(--orange);margin:20px auto 0}
.about .section-title{padding-top:76px}
.about-lead{font-size:16px;font-weight:600;color:var(--ink);line-height:27px;width:930px;margin:40px auto 0}
.about-body{font-size:14px;line-height:26px;width:940px;margin:18px auto 0}
.btn-row{display:flex;justify-content:center;gap:20px;margin-top:38px}
.btn{font-size:15px;font-weight:600;padding:12px 20px;text-transform:uppercase;height:46px}
.btn-solid{background:var(--orange);color:var(--white);border:2px solid var(--orange)}
.btn-outline{border:2px solid var(--ink);color:var(--ink)}

/* commercial */
.commercial{height:535px;background:var(--cream)}
.commercial-copy{position:absolute;left:99px;top:72px;width:590px}
.block-title{font-size:29px;font-weight:600;color:var(--orange)}
.commercial-lead{font-size:15px;font-weight:600;color:var(--ink);line-height:24px;margin-top:18px}
.feature-grid{display:grid;grid-template-columns:300px 290px;row-gap:30px;margin-top:24px}
.feature h3{font-size:18px;font-weight:600;color:var(--orange);display:flex;align-items:center;gap:8px}
.feature p{font-size:13px;line-height:21px;margin-top:12px;width:275px}
.photo-slant{position:absolute}

/* values */
.values{height:535px}
.values-copy{position:absolute;left:516px;top:112px;width:590px}
.values-copy p{font-size:14.5px;line-height:24px;margin-top:14px}
.value-list{list-style:none;margin-top:24px}
.value-list li{font-size:14.5px;line-height:29px;display:flex;align-items:center;gap:14px}

/* tour form */
.tour{height:547px;background:linear-gradient(180deg,#2c2c2c,#363636 50%,#2a2a2a)}
.tour .title-light{color:var(--white);font-size:28px;font-weight:700;text-align:center;padding-top:78px;text-transform:uppercase}
.tour .rule{background:var(--white);width:160px;margin-top:20px}
.tour-form{position:absolute;left:99px;top:195px;width:1000px;display:grid;grid-template-columns:repeat(3,324px);column-gap:14px;row-gap:22px}
.field{height:46px;border:2px solid var(--white);color:var(--white);font-size:15px;font-weight:600;display:flex;align-items:center;justify-content:space-between;padding:0 12px}
.field.wide{grid-column:span 2}
.submit{position:absolute;left:437px;top:406px;width:324px;height:48px;background:var(--white);color:var(--orange);font-size:15px;font-weight:600;display:flex;align-items:center;justify-content:center;text-transform:uppercase}

/* locations */
.locations-band{height:68px;background:var(--orange);color:var(--white);font-size:28px;font-weight:700;text-align:center;line-height:68px;text-transform:uppercase}
.locations{height:639px}
.world-map{position:absolute;left:20px;top:40px;width:1130px;height:560px;border-radius:40px;background:var(--map)}
.map-dot{position:absolute;border-radius:50%;background:var(--orange)}
.legend{position:absolute;left:99px;top:440px;list-style:none}
.legend li{display:flex;align-items:center;gap:12px;font-size:16px;font-weight:700;color:var(--ink);height:34px}
.legend .swatch{display:flex;justify-content:center;width:36px}

/* testimonials */
.testimonials{height:499px;background:var(--grey-bg);text-align:center}
.testimonials .section-title{padding-top:74px}
.quote-row{position:absolute;left:99px;top:203px;display:flex;gap:20px}
.quote{width:322px;text-align:left}
.quote-box{position:relative;height:169px;border:2px solid #e0644a;background:var(--white);padding:48px 22px 0;font-size:13.5px;line-height:21px;color:#444}
.quote-box .badge{position:absolute;left:144px;top:-17px;width:34px;height:34px;border-radius:50%;background:var(--orange);border:3px solid var(--white);display:flex;align-items:center;justify-content:center}
.quote.featured .quote-box{background:var(--orange);color:var(--white);border-color:var(--orange)}
.quote-name{font-size:16px;font-weight:600;color:var(--ink);margin:16px 0 0 28px}
.quote.featured .quote-name{color:var(--orange)}
.carousel-arrow{position:absolute;top:290px}

/* footer */
.site-footer{height:309px;background:var(--dark);text-align:center;color:var(--white)}
.social{display:flex;justify-content:center;gap:9px;padding-top:78px}
.social span{width:38px;height:38px;border-radius:50%;border:2px solid var(--white)}
.footer-nav{margin-top:36px;font-size:15px;font-weight:600;letter-spacing:.5px;text-transform:uppercase}
.footer-nav span{padding:0 12px}
.footer-rule{width:1000px;height:1px;background:#555;margin:28px auto 0}
.copyright{font-size:15px;font-weight:600;margin-top:32px}
</style>
</head>
<body>

<header class="site-header">
  <div class="brand">DeskHarbor</div>
  <nav class="main-nav">
    <a class="active">Home</a><a>Locations</a><a>Enterprise</a><a>Special promotions</a><a>Blog</a><a>Contact us</a><a>About us</a>
  </nav>
</header>

<section class="hero">
  <div class="hero-photo" role="img" aria-label="Photo of a modern open-plan coworking office with white desks and dark chairs"></div>
  <div class="hero-copy">
    <div class="hero-title">DeskHarbor</div>
    <div class="hero-tag">Brandpersonality</div>
    <div class="btn-outline-light">Read more</div>
  </div>
  <div class="slider-dots"><span class="on"></span><span></span><span></span><span></span><span></span></div>
  <svg class="scroll-notch" width="80" height="42" viewBox="0 0 80 42">
    <polygon points="0,0 40,0 80,0 80,42 0,42" fill="none"/>
    <polygon points="0,42 40,6 80,42" fill="#fff" transform="rotate(180 40 24)"/>
    <polygon points="0,0 80,0 80,42 0,42" fill="none"/>
    <polyline points="28,16 40,28 52,16" fill="none" stroke="#f5874a" stroke-width="4"/>
  </svg>
</section>

<section class="about">
  <h2 class="section-title">About DeskHarbor co-working</h2>
  <div class="rule"></div>
  <p class="about-lead">DeskHarbor is a new global coworking brand, growing fast and establishing stylish locations and communities that inspire innovation and collaboration all around the world.</p>
  <p class="about-body">The company targets customers ranging from small-medium firms and up to global enterprises, who need a space to grow in and seek a community with a collaborative spirit. Coworking is a style of work that involves a shared working environment. Unlike in a typical office environment, those coworking are usually employed by various organizations.</p>
  <div class="btn-row"><span class="btn btn-solid">Read more</span><span class="btn btn-outline">Contact us</span></div>
</section>

<section class="commercial">
  <div class="commercial-copy">
    <h2 class="block-title">Commercial Projects</h2>
    <p class="commercial-lead">Coworking is not only about the physical place, but about establishing and being part of a community.</p>
    <div class="feature-grid">
      <div class="feature"><h3><svg width="20" height="20" viewBox="0 0 20 20"><circle cx="10" cy="9" r="5" fill="none" stroke="#f5874a" stroke-width="2"/><path d="M8 16h4M10 1v2M2 9h2M16 9h2M4 3l1.5 1.5M16 3l-1.5 1.5" stroke="#f5874a" stroke-width="2"/></svg>Space as an Experience</h3><p>The project includes a complete website design, focused on delivering the company's values and messages, provide information.</p></div>
      <div class="feature"><h3><svg width="20" height="20" viewBox="0 0 20 20"><circle cx="10" cy="9" r="5" fill="none" stroke="#f5874a" stroke-width="2"/><path d="M8 16h4M10 1v2M2 9h2M16 9h2M4 3l1.5 1.5M16 3l-1.5 1.5" stroke="#f5874a" stroke-width="2"/></svg>Beyond Four Walls</h3><p>The project includes a complete website design, focused on delivering the company's values and messages, provide information.</p></div>
      <div class="feature"><h3><svg width="20" height="20" viewBox="0 0 20 20"><circle cx="10" cy="9" r="5" fill="none" stroke="#f5874a" stroke-width="2"/><path d="M8 16h4M10 1v2M2 9h2M16 9h2M4 3l1.5 1.5M16 3l-1.5 1.5" stroke="#f5874a" stroke-width="2"/></svg>Workspace Is Our Craft</h3><p>The project includes a complete website design, focused on delivering the company's values and messages, provide information.</p></div>
      <div class="feature"><h3><svg width="20" height="20" viewBox="0 0 20 20"><circle cx="10" cy="9" r="5" fill="none" stroke="#f5874a" stroke-width="2"/><path d="M8 16h4M10 1v2M2 9h2M16 9h2M4 3l1.5 1.5M16 3l-1.5 1.5" stroke="#f5874a" stroke-width="2"/></svg>Practice Makes Perfect</h3><p>The project includes a complete website design, focused on delivering the company's values and messages, provide information.</p></div>
    </div>
  </div>
  <svg class="photo-slant" style="left:732px;top:0" width="468" height="535" viewBox="0 0 468 535" role="img" aria-label="Photo of a bright office workstation with monitors and an office chair">
    <defs><linearGradient id="officeLight" x1="0" y1="0" x2="1" y2="1"><stop offset="0" stop-color="#e8e8e6"/><stop offset=".5" stop-color="#b9b9b6"/><stop offset="1" stop-color="#8e8e8c"/></linearGradient></defs>
    <polygon points="0,110 468,30 468,535 0,440" fill="url(#officeLight)"/>
  </svg>
</section>

<section class="values">
  <svg class="photo-slant" style="left:0;top:0" width="470" height="535" viewBox="0 0 470 535" role="img" aria-label="Photo of a coworking hall with long desks and red chairs">
    <defs><linearGradient id="hallTone" x1="0" y1="0" x2="1" y2="1"><stop offset="0" stop-color="#8a8782"/><stop offset=".5" stop-color="#6b5a4c"/><stop offset="1" stop-color="#3e3028"/></linearGradient></defs>
    <polygon points="0,0 300,0 470,190 470,400 0,535" fill="url(#hallTone)"/>
  </svg>
  <div class="values-copy">
    <h2 class="block-title">Values To Deliver</h2>
    <p>Coworking is a style of work that involves a shared working environment. Unlike in a typical office environment, those coworking are usually employed by various organizations. Coworking is a gathering of a group of people who are working independently, but who share values, and who are interested.</p>
    <ul class="value-list">
      <li><svg width="14" height="14"><circle cx="7" cy="7" r="6" fill="none" stroke="#f5874a" stroke-width="2"/><path d="M5 4l3 3-3 3" fill="none" stroke="#f5874a" stroke-width="2"/></svg>Inspire collaboration &amp; innovation</li>
      <li><svg width="14" height="14"><circle cx="7" cy="7" r="6" fill="none" stroke="#f5874a" stroke-width="2"/><path d="M5 4l3 3-3 3" fill="none" stroke="#f5874a" stroke-width="2"/></svg>Idea sharing</li>
      <li><svg width="14" height="14"><circle cx="7" cy="7" r="6" fill="none" stroke="#f5874a" stroke-width="2"/><path d="M5 4l3 3-3 3" fill="none" stroke="#f5874a" stroke-width="2"/></svg>Be a part of an exclusive club</li>
      <li><svg width="14" height="14"><circle cx="7" cy="7" r="6" fill="none" stroke="#f5874a" stroke-width="2"/><path d="M5 4l3 3-3 3" fill="none" stroke="#f5874a" stroke-width="2"/></svg>Realize your greatness</li>
      <li><svg width="14" height="14"><circle cx="7" cy="7" r="6" fill="none" stroke="#f5874a" stroke-width="2"/><path d="M5 4l3 3-3 3" fill="none" stroke="#f5874a" stroke-width="2"/></svg>Style and design awareness</li>
    </ul>
  </div>
</section>

<section class="tour">
  <h2 class="title-light">Book a location tour</h2>
  <div class="rule"></div>
  <div class="tour-form">
    <div class="field">First Name</div>
    <div class="field">Last Name</div>
    <div class="field">Street Address</div>
    <div class="field">City<svg width="12" height="8"><polygon points="0,0 12,0 6,8" fill="#fff"/></svg></div>
    <div class="field">State/Province<svg width="12" height="8"><polygon points="0,0 12,0 6,8" fill="#fff"/></svg></div>
    <div class="field">Zip Code<svg width="12" height="8"><polygon points="0,0 12,0 6,8" fill="#fff"/></svg></div>
    <div class="field wide">Email Address</div>
    <div class="field">DD/MM/YY<svg width="12" height="8"><polygon points="0,0 12,0 6,8" fill="#fff"/></svg></div>
  </div>
  <div class="submit">Submit here</div>
</section>

<div class="locations-band">Our work locations</div>

<section class="locations">
  <div class="world-map" role="img" aria-label="World map marking the cities with coworking locations"></div>
  <span class="map-dot" style="left:400px;top:68px;width:22px;height:22px"></span>
  <span class="map-dot" style="left:110px;top:100px;width:16px;height:16px"></span>
  <span class="map-dot" style="left:212px;top:210px;width:36px;height:36px"></span>
  <span class="map-dot" style="left:875px;top:60px;width:38px;height:38px"></span>
  <span class="map-dot" style="left:720px;top:210px;width:22px;height:22px"></span>
  <span class="map-dot" style="left:958px;top:220px;width:16px;height:16px"></span>
  <span class="map-dot" style="left:370px;top:350px;width:22px;height:22px"></span>
  <span class="map-dot" style="left:500px;top:302px;width:12px;height:12px"></span>
  <span class="map-dot" style="left:905px;top:340px;width:26px;height:26px"></span>
  <span class="map-dot" style="left:585px;top:405px;width:12px;height:12px"></span>
  <span class="map-dot" style="left:272px;top:481px;width:22px;height:22px"></span>
  <span class="map-dot" style="left:916px;top:475px;width:12px;height:12px"></span>
  <span class="map-dot" style="left:1065px;top:510px;width:14px;height:14px"></span>
  <ul class="legend">
    <li><span class="swatch"><svg width="36" height="36"><circle cx="18" cy="18" r="17" fill="#f5874a"/><text x="18" y="23" text-anchor="middle" font-family="Open Sans,sans-serif" font-size="13" font-weight="700" fill="#fff">10</text></svg></span>10 or more</li>
    <li><span class="swatch"><svg width="24" height="24"><circle cx="12" cy="12" r="11" fill="#f5874a"/></svg></span>3 or more</li>
    <li><span class="swatch"><svg width="14" height="14"><circle cx="7" cy="7" r="6" fill="#f5874a"/></svg></span>1-2</li>
  </ul>
</section>

<section class="testimonials">
  <h2 class="section-title">Our testimonials</h2>
  <div class="rule"></div>
  <svg class="carousel-arrow" style="left:40px" width="16" height="30"><polyline points="14,2 2,15 14,28" fill="none" stroke="#555" stroke-width="2"/></svg>
  <svg class="carousel-arrow" style="left:1144px" width="16" height="30"><polyline points="2,2 14,15 2,28" fill="none" stroke="#555" stroke-width="2"/></svg>
  <div class="quote-row">
    <div class="quote">
      <div class="quote-box"><span class="badge"><svg width="16" height="14"><path d="M1 2h14v8H6l-4 3v-3H1z" fill="#fff"/></svg></span>"Nemo enim ipsam voluptatem quia voluptas sit aspernatur aut odit aut fugit, sed quia co nsequuntur magni dolores eos qui ratione vo luptatem sequi nesciunt."</div>
      <div class="quote-name">Nina K.</div>
    </div>
    <div class="quote featured">
      <div class="quote-box"><span class="badge"><svg width="16" height="14"><path d="M1 2h14v8H6l-4 3v-3H1z" fill="#fff"/></svg></span>"Nemo enim ipsam voluptatem quia voluptas sit aspernatur aut odit aut fugit, sed quia co nsequuntur magni dolores eos qui ratione vo luptatem sequi nesciunt."</div>
      <div class="quote-name">Owen Hartley, London</div>
    </div>
    <div class="quote">
      <div class="quote-box"><span class="badge"><svg width="16" height="14"><path d="M1 2h14v8H6l-4 3v-3H1z" fill="#fff"/></svg></span>"Nemo enim ipsam voluptatem quia voluptas sit aspernatur aut odit aut fugit, sed quia co nsequuntur magni dolores eos qui ratione vo luptatem sequi nesciunt."</div>
      <div class="quote-name">Tessa L.</div>
    </div>
  </div>
</section>

<footer class="site-footer">
  <div class="social"><span></span><span></span><span></span><span></span><span></span></div>
  <div class="footer-nav"><span>Locations</span>|<span>Enterprise</span>|<span>Special promotions</span>|<span>Blog</span>|<span>Contact us</span>|<span>About us</span></div>
  <div class="footer-rule"></div>
  <p class="copyright">Copyrights © 2017 DeskHarbor. All Rights Reserved</p>
</footer>

</body>
</html>
```